Software Product Flyer Design

A established czech software company needs a marketing flyer to promote their software product and its modules.
The overall feel of the flyer must to be serious, but also eye-catching, enticing, clever and bold to attract customers.
Unifying graphic element is the new product logo.
The flyer would be A4, colour both sides and folded once (to give 4 pages of A5).
Title page - product logo with module name and module icon, short presentation of the product and list of its key features.
Inside pages - detailed informations with screenshots or graphical schemas.
Back side - informations about technical requirements and user support, contacts (address, phone, fax, e-mail, web pages - no social networks).
Product logo, module icon and some images attached.
Updates
Hello,
Reason: For organizational reasons we extending the deadline by 10 days.
FYI: We have uploaded the new ZIP file with previous version of our flyer.
Attached PDF file with text for inner pages.
Target Market(s)
Existing or new customers like municipalities, public authorities and nonprofit organizations.
Industry/Entity Type
Marketing
Requirements
Must have
- Winning designer must provide a template for Adobe InDesign based on his graphic design.
Avoid to using exotic fonts - in Czech we use Latin Extended characters (like áéěíýůčřžšťďň).
Nice to have
- Using graphic motif from product logo like as attached splash screen.

```html
<!DOCTYPE html>
<html lang="en">
<head>
<meta charset="utf-8">
<title>Product Flyer – Open Spread</title>
<link rel="stylesheet" href="https://fonts.googleapis.com/css2?family=Source+Sans+3:ital,wght@0,400;0,600;0,700;1,400&family=Arimo:wght@700&family=Crimson+Text:ital@1&display=swap">
<style>
  :root {
    --ink-dark: #4a4b50;
    --ink-darker: #3e3f44;
    --accent: #e8561a;
    --paper: #ffffff;
    --text: #2a2a2c;
    --stage: #dcdcdc;
    --sans: "Source Sans 3", "Myriad Pro", sans-serif;
    --bold-sans: "Arimo", Arial, sans-serif;
    --serif-italic: "Crimson Text", Georgia, serif;
  }
  * { box-sizing: border-box; margin: 0; padding: 0; }
  html, body { width: 1200px; height: 900px; overflow: hidden; background: var(--stage); }
  .spread { position: relative; width: 1200px; height: 900px; font-family: var(--sans); color: var(--text); }
  .page { position: absolute; top: 40px; width: 580px; height: 820px; background: var(--paper); overflow: hidden; box-shadow: 0 4px 14px rgba(0,0,0,.18); }
  .page--back { left: 20px; }
  .page--front { left: 600px; }
  .abs { position: absolute; }

  /* brand name stand-in */
  .brand { position: absolute; display: flex; align-items: center; gap: 8px; font-family: var(--sans); font-weight: 700; letter-spacing: -1px; line-height: 1; }
  .brand__dot { width: .42em; height: .42em; border-radius: 50%; background: var(--accent); }
  .brand--light { color: #fff; }
  .brand--dark { color: var(--ink-dark); }

  /* ---------- back page ---------- */
  .back-header { position: absolute; left: 0; top: 0; width: 580px; height: 230px; }
  .back-title { left: 30px; top: 64px; color: var(--accent); font-size: 30px; font-weight: 700; line-height: 1.1; }
  .back-intro { left: 30px; top: 100px; width: 330px; color: #fff; font-size: 12px; line-height: 1.25; }
  .badge { position: absolute; left: 452px; top: 18px; width: 110px; height: 110px; border-radius: 50%; background: var(--accent); display: flex; align-items: center; justify-content: center; }
  .badge::before { content: ""; position: absolute; inset: 6px; border: 2px solid #fff; border-radius: 50%; }
  .badge__text { color: #fff; text-align: center; font-size: 15px; line-height: 1.1; }
  .badge__text strong { display: block; font-size: 25px; font-weight: 700; }
  .col { position: absolute; font-size: 13px; line-height: 1.2; text-align: justify; }
  .col h2 { font-size: 18px; font-weight: 700; text-align: left; margin-bottom: 6px; }
  .col p + p { margin-top: 18px; }
  .col--left { left: 30px; top: 244px; width: 258px; }
  .col--right { left: 310px; top: 244px; width: 240px; }
  .col--right h3 { font-size: 12.5px; font-weight: 700; text-align: right; margin-bottom: 4px; }
  .dotted-list { list-style: none; border: 2px dotted var(--text); padding: 6px 10px 6px 12px; margin: 0 0 10px 10px; width: 176px; font-size: 11px; line-height: 1.15; text-align: left; white-space: nowrap; }
  .dotted-list li::before { content: ""; display: inline-block; width: 8px; height: 8px; background: var(--text); margin-right: 6px; vertical-align: -1px; }
  .web { left: 30px; top: 528px; color: var(--accent); font-size: 28px; font-weight: 600; }
  .block { position: absolute; top: 615px; height: 150px; }
  .block--accent { left: 30px; width: 235px; background: var(--accent); }
  .block--dark { left: 285px; width: 265px; background: var(--ink-dark); }

  /* ---------- front page ---------- */
  .front-column { position: absolute; left: 0; top: 0; width: 270px; height: 820px; background: linear-gradient(180deg, var(--ink-dark), var(--ink-darker)); }
  .front-rule { position: absolute; left: 270px; top: 0; width: 6px; height: 290px; background: var(--accent); }
  .main-title { left: 0; top: 100px; width: 270px; text-align: center; color: #fff; font-size: 31px; font-weight: 700; line-height: 1.12; }
  .main-title small { display: block; color: var(--accent); font-size: 17px; font-weight: 700; margin-top: 2px; }
  .lorem { left: 24px; top: 205px; width: 226px; color: #fff; font-family: var(--serif-italic); font-style: italic; font-size: 13px; line-height: 1.2; }
  .image-text { left: 20px; top: 400px; width: 164px; color: #fff; font-size: 13.5px; line-height: 1.22; text-align: center; }
  .image-text h3 { color: var(--accent); font-size: 15px; font-weight: 700; text-align: left; margin-bottom: 2px; }
  .screenshot { position: absolute; left: 20px; top: 628px; width: 222px; height: 172px; border: 5px solid #fff; background: linear-gradient(160deg, #f2f4f6, #c9ced4); display: flex; align-items: center; justify-content: center; }
  .screenshot span { font-family: var(--bold-sans); font-weight: 700; font-size: 28px; color: #111; transform: rotate(38deg); }
  .secondary { position: absolute; left: 284px; top: 0; width: 286px; height: 168px; background: var(--ink-dark); color: #fff; padding: 14px 14px 0 14px; }
  .secondary h2 { font-size: 22px; font-weight: 400; line-height: 1.15; margin-bottom: 8px; }
  .secondary p { font-size: 12.5px; line-height: 1.22; }
  .features { left: 290px; top: 180px; width: 270px; }
  .features h2 { font-family: var(--bold-sans); font-weight: 700; font-size: 21px; color: var(--ink-dark); padding-bottom: 4px; border-bottom: 2px solid var(--accent); }
  .features ul { list-style: none; margin-top: 8px; font-family: var(--bold-sans); font-weight: 700; font-size: 14px; line-height: 1.3; color: #111; }
  .features li::before { content: "▶"; font-size: 12px; margin-right: 8px; }
  .features-rule { left: 290px; top: 316px; width: 270px; height: 2px; background: var(--accent); }
  .bullets-title { left: 290px; top: 324px; font-family: var(--bold-sans); font-weight: 700; font-size: 14px; color: #111; }
  .bullets { position: absolute; top: 348px; left: 0; width: 580px; list-style: none; font-size: 13px; line-height: 16.5px; }
  .bullets li::before { content: ""; display: inline-block; width: 9px; height: 9px; background: var(--text); margin-right: 6px; vertical-align: -1px; }
  .focus { position: absolute; left: 190px; top: 383px; width: 166px; height: 166px; border-radius: 50%; background: #fff; display: flex; align-items: center; justify-content: center; }
  .focus__inner { width: 150px; height: 150px; border-radius: 50%; background: #141414; color: #fff; display: flex; flex-direction: column; align-items: center; justify-content: center; text-align: center; font-size: 15px; line-height: 1.2; }
  .focus__inner strong { font-size: 21px; font-weight: 700; margin-top: 3px; }
  .closing { left: 300px; top: 680px; width: 262px; font-size: 13px; line-height: 1.2; text-align: center; }
  .closing h2 { font-family: var(--bold-sans); font-weight: 700; font-size: 16px; color: #111; text-align: left; margin-bottom: 3px; }
  .footnote { left: 290px; top: 784px; width: 272px; border-top: 1px solid var(--text); padding-top: 3px; font-size: 9.5px; line-height: 1.15; }
</style>
</head>
<body>
<main class="spread">

  <!-- Back page -->
  <section class="page page--back" aria-label="Back page">
    <svg class="back-header" viewBox="0 0 580 230" aria-hidden="true">
      <path d="M0 0 H480 C470 150 380 200 0 205 Z" fill="#4a4b50"/>
      <path d="M0 205 C380 200 470 150 480 0 H496 C488 162 398 216 0 219 Z" fill="#e8561a"/>
    </svg>
    <div class="brand brand--light" style="left:28px; top:16px; font-size:44px;"><span class="brand__dot"></span>nodo</div>
    <h1 class="abs back-title">Text Title</h1>
    <p class="abs back-intro">Sed ut perspiciatis unde omnis iste natus error sit voluptatem accusantium doloremque laudantium, totam rem aperiam, eaque ipsa quae ab illo inventore veritatis et quasi architecto beatae vitae dicta sunt explicabo.</p>
    <div class="badge"><p class="badge__text">Any Text<strong>HERE</strong></p></div>

    <div class="col col--left">
      <h2>Any Title Can Be Here</h2>
      <p>Sed ut perspiciatis unde omnis iste natus error sit voluptatem accusantium doloremque laudantium, totam rem aperiam, eaque ipsa quae ab illo inventore veritatis et quasi architecto beatae vitae dicta sunt explicabo.</p>
      <p>Sed ut perspiciatis unde omnis iste natus error sit voluptatem accusantium doloremque laudantium, totam rem aperiam, eaque ipsa quae ab illo inventore veritatis et quasi architecto beatae vitae dicta sunt explicabo.</p>
    </div>
    <div class="col col--right">
      <h3>Some Bulleted text could be here</h3>
      <ul class="dotted-list">
        <li>Sed ut perspiciatis unde</li><li>Sed ut perspiciatis unde</li><li>Sed ut perspiciatis unde</li><li>Sed ut perspiciatis unde</li><li>Sed ut perspiciatis unde</li><li>Sed ut perspiciatis unde</li><li>Sed ut perspiciatis unde</li><li>Sed ut perspiciatis unde</li><li>Sed ut perspiciatis unde</li><li>Sed ut perspiciatis unde</li>
      </ul>
      <p>Sed ut perspiciatis unde omnis iste natus error sit voluptatem accusantium doloremque laudantium, totam rem aperiam, eaque ipsa quae ab illo inventore veritatis et quasi architecto beatae vitae dicta sunt explicabo.</p>
    </div>
    <p class="abs web">www.webaddress.com</p>
    <div class="block block--accent"></div>
    <div class="block block--dark"></div>
  </section>

  <!-- Front page -->
  <section class="page page--front" aria-label="Front page">
    <div class="front-column"></div>
    <div class="front-rule"></div>
    <div class="brand brand--light" style="left:26px; top:22px; font-size:54px;"><span class="brand__dot"></span>nodo</div>
    <h1 class="abs main-title">Main<br>Title will Here<small>any subtitle here</small></h1>
    <p class="abs lorem">Lorem ipsum dolor sit amet, consectetur adipisicing elit, sed do eiusmod tempor incididunt ut labore et dolore magna aliqua. Ut enim ad minim veniam, quis nostrud exercitation ullamco laboris nisi ut aliquip ex ea commodo consequat. Duis aute irure dolor in reprehenderit in voluptate velit esse cillum dolore eu fugiat nulla pariatur. Excepteur sint occaecat cupidatat non proident, sunt in culpa qui officia deserunt mollit anim id est laborum.</p>
    <div class="abs image-text">
      <h3>Image Related Text</h3>
      <p>Sed ut perspiciatis unde omnis iste natus error sit voluptatem accusantium doloremque laudantium, totam rem aperiam, eaque ipsa quae ab illo inventore veritatis et quasi architecto beatae vitae dicta sunt.</p>
    </div>
    <div class="screenshot" role="img" aria-label="Software screenshot placeholder"><span>Any Image</span></div>

    <div class="secondary">
      <h2>Here May be Another Secondary Title</h2>
      <p>Sed ut perspiciatis unde omnis iste natus error sit voluptatem accusantium doloremque laudantium, totam rem aperiam, eaque ipsa quae ab illo inventore veritatis et quasi architecto beatae vitae dicta sunt explicabo.</p>
    </div>
    <div class="abs features">
      <h2>Key Features</h2>
      <ul>
        <li>Here will go key feature</li><li>Here will go key feature</li><li>Here will go key feature</li><li>Here will go key feature</li>
      </ul>
    </div>
    <div class="abs features-rule"></div>
    <p class="abs bullets-title">Some Bulleted Text Area.</p>
    <ul class="bullets">
      <li style="margin-left:304px">Sed ut perspiciatis unde</li>
      <li style="margin-left:322px">Sed ut perspiciatis unde</li>
      <li style="margin-left:338px">Sed ut perspiciatis unde</li>
      <li style="margin-left:350px">Sed ut perspiciatis unde</li>
      <li style="margin-left:360px">Sed ut perspiciatis unde</li>
      <li style="margin-left:366px">Sed ut perspiciatis unde</li>
      <li style="margin-left:368px">Sed ut perspiciatis</li>
      <li style="margin-left:366px">Sed ut perspiciatis unde</li>
      <li style="margin-left:360px">Sed ut perspiciatis unde</li>
      <li style="margin-left:354px">Sed ut perspiciatis unde</li>
      <li style="margin-left:346px">Sed ut perspiciatis unde</li>
    </ul>
    <div class="focus"><div class="focus__inner">Some text that<br>need to be<strong>FOCUSED</strong></div></div>

    <div class="brand brand--dark" style="left:388px; top:600px; font-size:50px;"><span class="brand__dot"></span>nodo</div>
    <div class="abs closing">
      <h2>Another Title or Anything</h2>
      <p>Sed ut perspiciatis unde omnis iste natus error sit voluptatem accusantium doloremque laudantium, totam rem aperiam, eaque ipsa quae ab illo inventore veritatis et quasi architecto beatae vitae dicta sunt explicabo.</p>
    </div>
    <p class="abs footnote">Sed ut perspiciatis unde omnis iste natus error sit voluptatem accusantium doloremque laudantium, totam rem aperiam</p>
  </section>

</main>
</body>
</html>
```